label design for soy candle

I am a start up making soy candles and other products involving scents.
On the label should be in writing : the scent, Handgemacht in der Schweiz, Sojakerze, my logo with the name Pellwick Candles on it. I will upload the currant label of my candles, but I want something more fashioned. The color of the label should be black with the scent written in gold, and the rest in white. Or maybe suggest something different, I am open to new designs. I am also open to change the logo, except the flower has to stay.
Sizes : square 60x60mm / round 50mm / rectangle 70x20mm ( for different jars )

```html
<!DOCTYPE html>
<html lang="de">
<head>
<meta charset="utf-8">
<title>Pellwick Candles – Citrus Basil Etikett</title>
<link rel="stylesheet" href="https://fonts.googleapis.com/css2?family=Cormorant+Garamond:wght@500;600;700&display=swap">
<style>
  :root {
    --stage: #050505;
    --panel: #2b2529;
    --panel-deep: #231e22;
    --foil: #9dbf6a;
    --foil-light: #c9dca0;
    --marble-dark: #2a2326;
  }
  * { margin: 0; padding: 0; box-sizing: border-box; }
  html, body {
    width: 1200px;
    height: 960px;
    overflow: hidden;
    background: var(--stage);
  }
  .canvas {
    position: relative;
    width: 1200px;
    height: 960px;
    display: flex;
    align-items: center;
    justify-content: center;
  }
  /* Square label, 60 x 60 mm */
  .label {
    position: relative;
    width: 720px;
    height: 720px;
  }
  .label__marble {
    position: absolute;
    inset: 0;
    background:
      radial-gradient(ellipse at 20% 15%, rgba(201,220,160,0.55), transparent 45%),
      radial-gradient(ellipse at 85% 30%, rgba(157,191,106,0.45), transparent 40%),
      radial-gradient(ellipse at 15% 75%, rgba(157,191,106,0.5), transparent 42%),
      radial-gradient(ellipse at 80% 90%, rgba(201,220,160,0.45), transparent 45%),
      linear-gradient(135deg, #4b5a34 0%, var(--marble-dark) 35%, #5f7440 60%, var(--marble-dark) 100%);
  }
  .label__panel {
    position: absolute;
    left: 70px;
    top: 70px;
    width: 580px;
    height: 580px;
    background:
      repeating-linear-gradient(0deg, rgba(255,255,255,0.018) 0 1px, transparent 1px 3px),
      repeating-linear-gradient(90deg, rgba(0,0,0,0.06) 0 1px, transparent 1px 3px),
      linear-gradient(180deg, var(--panel) 0%, var(--panel-deep) 100%);
    border: 3px solid var(--foil);
    color: var(--foil);
    font-family: "Cormorant Garamond", serif;
    font-variant-numeric: lining-nums;
    text-align: center;
    text-transform: uppercase;
  }
  .brand {
    position: absolute;
    top: 42px;
    left: 0;
    right: 0;
    display: flex;
    flex-direction: column;
    align-items: center;
    gap: 18px;
  }
  .brand__mark {
    width: 58px;
    height: 58px;
    border-radius: 50%;
    background: var(--foil);
  }
  .brand__name {
    font-weight: 600;
    font-size: 27px;
    line-height: 1;
    letter-spacing: 0.5px;
    color: var(--foil);
  }
  .scent {
    position: absolute;
    top: 245px;
    left: 0;
    right: 0;
    font-weight: 700;
    font-size: 64px;
    line-height: 1;
    letter-spacing: -0.5px;
    color: var(--foil-light);
  }
  .scent-rule {
    position: absolute;
    top: 326px;
    left: 118px;
    right: 118px;
    height: 1.5px;
    background: var(--foil);
  }
  .product-type {
    position: absolute;
    top: 348px;
    left: 0;
    right: 0;
    font-weight: 600;
    font-size: 17px;
    line-height: 1;
    letter-spacing: 0.5px;
  }
  .origin {
    position: absolute;
    top: 490px;
    left: 0;
    right: 0;
    font-weight: 700;
    font-size: 20px;
    line-height: 1;
  }
  .volume {
    position: absolute;
    top: 522px;
    left: 0;
    right: 0;
    font-weight: 700;
    font-size: 14px;
    line-height: 1;
    letter-spacing: 0.5px;
  }
</style>
</head>
<body>
  <main class="canvas">
    <section class="label">
      <div class="label__marble" role="img" aria-label="Marmoriertes Wirbelmuster in dunklem Pflaume mit grüngoldenen Folienadern"></div>
      <div class="label__panel">
        <div class="brand">
          <span class="brand__mark"></span>
          <span class="brand__name">Pellwick Candles</span>
        </div>
        <h1 class="scent">Citrus Basil</h1>
        <div class="scent-rule"></div>
        <p class="product-type">Vegane Sojakerze</p>
        <p class="origin">Handgemacht in der Schweiz</p>
        <p class="volume">8 oz &nbsp;|&nbsp; 237 ml</p>
      </div>
    </section>
  </main>
</body>
</html>
```